automotive repair and collision repair shop card

our company is called K.L Motor service we are a automotive repair company
we also do government inspections. the company information is on the cards. I would like you to use my new logo and create a new card and use the information from my old card. Good Luck!!

Industry/Entity Type

Car Repair

Contact Information for Business Card

Address: #417-18842 52 Ave, Surrey, BC V5K 8R3
Phone:(604) 555-0187
fax 604 555 0193
website www.klmotorworks.example

Font styles to use
Serif
Sans Serif

Requirements
Must have
• all the information
Should not have
• the owner and there name

```html
<!DOCTYPE html>
<html lang="en">
<head>
<meta charset="utf-8">
<title>K.L Motor service – Business Card</title>
<link href="https://fonts.googleapis.com/css2?family=Open+Sans:ital,wght@0,400;0,600;1,600&display=swap" rel="stylesheet">
<style>
  :root {
    --page-bg: #e9e7e3;
    --card-black: #121212;
    --card-black-edge: #2a2a2a;
    --card-grey: #b7b8ba;
    --band-dark: #1c1c1c;
    --band-bevel: #5a5a5a;
    --divider: #8d8e90;
    --ink-dark: #1d1d1d;
    --ink-light: #f4f4f4;
    --art-dark-a: #3a3a3a;
    --art-dark-b: #1a1a1a;
    --art-light-a: #9a9b9d;
    --art-light-b: #5e5f61;
  }
  * { box-sizing: border-box; margin: 0; padding: 0; }
  html, body {
    width: 1200px; height: 900px; overflow: hidden;
    background: var(--page-bg);
    font-family: "Open Sans", sans-serif;
  }
  .canvas { position: relative; width: 1200px; height: 900px; }

  .card {
    position: absolute; left: 290px; width: 620px; height: 350px;
    border-radius: 16px; overflow: hidden;
    box-shadow: 0 10px 28px rgba(0,0,0,.28);
  }

  /* Front */
  .card-front { top: 60px; background: var(--card-black); }
  .card-front .top-edge {
    position: absolute; left: 0; right: 0; top: 0; height: 8px;
    background: linear-gradient(var(--card-black-edge), var(--card-black));
  }
  .card-front .bottom-strip {
    position: absolute; left: 0; right: 0; bottom: 0; height: 26px;
    background: linear-gradient(#9c9d9f, #c4c5c7);
  }
  .front-art {
    position: absolute; left: 150px; top: 40px; width: 320px; height: 120px;
    border-radius: 60px 60px 20px 20px;
    background: linear-gradient(180deg, var(--art-dark-a), var(--art-dark-b));
  }
  .front-brand {
    position: absolute; left: 0; right: 0; top: 172px; text-align: center;
    color: var(--ink-light);
  }
  .brand-name {
    font-weight: 600; font-size: 34px; letter-spacing: 1px; text-transform: uppercase;
    line-height: 1.1;
  }
  .brand-tagline {
    font-weight: 600; font-style: italic; font-size: 14px; margin-top: 4px;
  }

  /* Back */
  .card-back { top: 470px; background: var(--card-grey); }
  .card-back svg.shapes { position: absolute; inset: 0; }
  .contact-list {
    position: absolute; left: 32px; top: 118px; list-style: none;
    color: var(--ink-dark); font-size: 15px; font-weight: 600;
  }
  .contact-list li { display: flex; align-items: center; height: 25px; white-space: nowrap; }
  .contact-list svg { width: 16px; height: 16px; margin-right: 14px; flex: none; }
  .back-art {
    position: absolute; left: 350px; top: 50px; width: 220px; height: 70px;
    border-radius: 40px 40px 12px 12px;
    background: linear-gradient(180deg, var(--art-light-a), var(--art-light-b));
  }
  .back-brand {
    position: absolute; left: 330px; width: 270px; top: 128px; text-align: right;
    color: var(--ink-dark);
  }
  .back-brand .brand-name { font-size: 24px; letter-spacing: .5px; white-space: nowrap; }
  .back-brand .brand-tagline { font-size: 12px; margin-top: 2px; }
  .address {
    position: absolute; right: 28px; top: 282px;
    color: var(--ink-light); font-size: 14px; font-weight: 600;
  }
</style>
</head>
<body>
<main class="canvas">

  <section class="card card-front" aria-label="Card front">
    <div class="top-edge"></div>
    <div class="front-art" role="img" aria-label="Line illustration of a sports car"></div>
    <div class="front-brand">
      <div class="brand-name">K.L Motor service</div>
      <div class="brand-tagline">One Stop Repair Shop</div>
    </div>
    <div class="bottom-strip"></div>
  </section>

  <section class="card card-back" aria-label="Card back">
    <svg class="shapes" viewBox="0 0 620 350" width="620" height="350" aria-hidden="true">
      <rect x="0" y="0" width="620" height="24" fill="var(--band-dark)"/>
      <rect x="0" y="24" width="620" height="4" fill="var(--band-bevel)"/>
      <line x1="295" y1="50" x2="318" y2="200" stroke="var(--divider)" stroke-width="1.5"/>
      <path d="M0,318 L255,318 C285,318 282,238 318,238 L620,238 L620,350 L0,350 Z"
            fill="var(--band-dark)" stroke="var(--band-bevel)" stroke-width="4"/>
    </svg>

    <ul class="contact-list">
      <li>
        <svg viewBox="0 0 16 16"><rect x="2" y="6" width="12" height="7" rx="1.5" fill="#fff"/><rect x="4" y="2" width="8" height="4" fill="#fff"/></svg>
        604 555 0193
      </li>
      <li>
        <svg viewBox="0 0 16 16"><path d="M4 1.5 L6.5 4.5 L5 6.5 C6 8.8 7.5 10.3 9.5 11 L11.5 9.5 L14.5 12 L12.5 14.5 C7 14 2 9 1.5 3.5 Z" fill="#fff"/></svg>
        (604) 555-0187
      </li>
      <li>
        <svg viewBox="0 0 16 16"><rect x="1.5" y="3.5" width="13" height="9" fill="none" stroke="#fff" stroke-width="1.4"/><path d="M1.5 3.5 L8 9 L14.5 3.5" fill="none" stroke="#fff" stroke-width="1.4"/></svg>
        info@klmotorworks.example
      </li>
      <li>
        <svg viewBox="0 0 16 16"><g fill="none" stroke="#fff" stroke-width="1.2"><circle cx="8" cy="8" r="6.3"/><ellipse cx="8" cy="8" rx="2.8" ry="6.3"/><line x1="1.7" y1="8" x2="14.3" y2="8"/></g></svg>
        www.klmotorworks.example
      </li>
    </ul>

    <div class="back-art" role="img" aria-label="Illustration of a sports car"></div>
    <div class="back-brand">
      <div class="brand-name">K.L Motor service</div>
      <div class="brand-tagline">One Stop Repair Shop</div>
    </div>

    <p class="address">#417-18842 52 Ave, Surrey, BC V5K 8R3</p>
  </section>

</main>
</body>
</html>
```